Northfield Builders Guild Business card

We are looking for a new business card design with photo included.
Our business is a nonprofit construction contractor membership organization. We offer business education, assist with business setup and licensing, provide safety training, and provide a member directory.
URL: www.builderslinkguild.org
Color code:
CMYK: 0 cyan, 42 magenta, 100 yellow, 0 black for Print.
Hexidecimal: #FF9900
RGB: R 255; G 153; B 0

```html
<!DOCTYPE html>
<html lang="en">
<head>
<meta charset="utf-8">
<title>Northfield Builders Guild – Business Card</title>
<link href="https://fonts.googleapis.com/css2?family=Poppins:wght@400;500;800&display=swap" rel="stylesheet">
<style>
  :root {
    --orange: #ff9900;
    --charcoal: #2f2f2f;
    --ink: #2b2b2b;
    --paper: #f4f4f2;
    --stage: #d9d9d9;
  }
  * { box-sizing: border-box; margin: 0; padding: 0; }
  html, body { width: 1200px; height: 900px; overflow: hidden; }
  body {
    background: var(--stage);
    font-family: "Poppins", sans-serif;
    display: flex;
    flex-direction: column;
    align-items: center;
    justify-content: center;
    gap: 24px;
  }
  .card {
    width: 700px;
    height: 400px;
    position: relative;
    overflow: hidden;
  }
  /* Front */
  .card-front { background: var(--paper); color: var(--ink); }
  .edge-band-dark {
    position: absolute; left: 0; top: 0; bottom: 0; width: 14px;
    background: var(--charcoal);
  }
  .edge-band-orange {
    position: absolute; left: 22px; top: 0; bottom: 0; width: 14px;
    background: var(--orange);
  }
  .brand-name {
    position: absolute; left: 84px; top: 70px;
    font-weight: 800; font-size: 40px; line-height: 1.02;
    letter-spacing: -0.5px; text-transform: uppercase;
    color: var(--ink);
  }
  .contact-list {
    position: absolute; left: 90px; top: 220px;
    list-style: none; font-size: 17px; line-height: 27px;
  }
  .contact-list li { display: flex; align-items: center; gap: 12px; }
  .contact-list svg { width: 17px; height: 17px; flex: none; }
  .address {
    position: absolute; left: 90px; top: 318px;
    font-size: 17px; line-height: 25px; font-style: normal;
  }
  .portrait-frame {
    position: absolute; right: 70px; top: 44px;
    width: 140px; height: 152px;
    border: 2px solid var(--orange);
    padding: 4px;
  }
  .portrait {
    width: 100%; height: 100%;
    background: linear-gradient(160deg, #e8e4e0 0%, #b08a6e 45%, #3a2b24 100%);
  }
  .person {
    position: absolute; right: 70px; top: 214px; text-align: right;
  }
  .person-name { font-weight: 500; font-size: 20px; line-height: 1.2; }
  .person-title { font-weight: 400; font-size: 16px; }
  /* Back */
  .card-back {
    background: var(--charcoal);
    border-bottom: 3px solid var(--orange);
    display: flex; align-items: center; justify-content: center;
  }
  .back-brand {
    font-weight: 800; font-size: 50px; line-height: 1.02;
    text-transform: uppercase; letter-spacing: -0.5px;
    color: var(--orange); text-align: center;
  }
</style>
</head>
<body>

  <section class="card card-front">
    <div class="edge-band-dark"></div>
    <div class="edge-band-orange"></div>

    <div class="brand-name">Northfield<br>Builders Guild</div>

    <ul class="contact-list">
      <li>
        <svg viewBox="0 0 24 24" fill="none" stroke="var(--orange)" stroke-width="2" stroke-linecap="round" stroke-linejoin="round"><path d="M5 3h4l2 5-3 2a12 12 0 0 0 6 6l2-3 5 2v4a2 2 0 0 1-2 2A18 18 0 0 1 3 5a2 2 0 0 1 2-2z"/></svg>
        (555) 014-2290
      </li>
      <li>
        <svg viewBox="0 0 24 24" fill="none" stroke="var(--orange)" stroke-width="2" stroke-linejoin="round"><rect x="3" y="5" width="18" height="14" rx="1"/><path d="M3 6l9 7 9-7"/></svg>
        info@builderslinkguild.org
      </li>
      <li>
        <svg viewBox="0 0 24 24" fill="none" stroke="var(--orange)" stroke-width="2"><circle cx="12" cy="12" r="9"/><path d="M3 12h18M12 3c3 3 3 15 0 18M12 3c-3 3-3 15 0 18"/></svg>
        www.builderslinkguild.org
      </li>
    </ul>

    <address class="address">2400 Millbrook Avenue<br>Northfield, OR 97000</address>

    <div class="portrait-frame">
      <div class="portrait" role="img" aria-label="Portrait photo of the director"></div>
    </div>

    <div class="person">
      <div class="person-name">Dana Whitfield</div>
      <div class="person-title">Director</div>
    </div>
  </section>

  <section class="card card-back">
    <div class="back-brand">Northfield<br>Builders Guild</div>
  </section>

</body>
</html>
```